Business Card Design Project

Looking for a simple and stylish business card. We are an Advertising Company. The card Must feature the company logo (attached) and also this info.
p: 0481552306
e: sales@rt-media.com.au
w: www.rt-media.com.au
We Advertise mainly using TV screens featured in restaurants and cafe. See website for more about the business.
Not really looking for a plain background, but at the same time do not want to much happening in the Background. I am not really to fussy though with the design or the colour scheme, and I am leaving the creativity part up to you creative designers.

```html
<!DOCTYPE html>
<html lang="en">
<head>
<meta charset="utf-8">
<title>RTMEDIA Business Card</title>
<link rel="stylesheet" href="https://fonts.googleapis.com/css2?family=Mulish:wght@300;400;500&display=swap">
<style>
  :root {
    --stage: #e6e7e9;
    --paper: #f7f7f7;
    --brand-blue: #1a5aa8;
    --deep-blue: #0a5aa8;
    --light-blue: #1e7dc8;
    --brand-pink: #e0215f;
    --ink: #3a3a3a;
    --white: #ffffff;
  }
  * { box-sizing: border-box; margin: 0; padding: 0; }
  html, body {
    width: 1200px;
    height: 900px;
    overflow: hidden;
    background: var(--stage);
    font-family: "Mulish", Arial, sans-serif;
  }
  .stage {
    position: relative;
    width: 1200px;
    height: 900px;
  }
  .card {
    position: absolute;
    left: 250px;
    width: 700px;
    height: 400px;
    overflow: hidden;
    box-shadow: 0 6px 18px rgba(0,0,0,0.18);
  }
  /* Back of card */
  .card-back {
    top: 40px;
    background: var(--deep-blue);
  }
  .card-back .backdrop {
    position: absolute;
    inset: 0;
    background: linear-gradient(160deg, var(--light-blue) 0%, var(--deep-blue) 60%, #0a4f96 100%);
  }
  .card-back .wordmark {
    position: absolute;
    left: 0;
    right: 0;
    top: 150px;
    text-align: center;
    font-size: 92px;
    font-weight: 300;
    letter-spacing: 4px;
    color: var(--white);
    line-height: 1;
  }
  /* Front of card */
  .card-front {
    top: 465px;
    background: var(--paper);
  }
  .card-front .wordmark {
    position: absolute;
    left: 0;
    right: 0;
    top: 38px;
    text-align: center;
    font-size: 84px;
    font-weight: 300;
    letter-spacing: 4px;
    color: var(--brand-blue);
    line-height: 1;
  }
  .details {
    position: absolute;
    left: 210px;
    top: 158px;
    height: 140px;
    padding-left: 30px;
    border-left: 2px solid var(--brand-blue);
    color: var(--ink);
  }
  .person-name {
    font-size: 30px;
    font-weight: 400;
    letter-spacing: 0.5px;
    line-height: 1.1;
  }
  .person-role {
    font-size: 20px;
    font-weight: 400;
    letter-spacing: 0.5px;
    margin-top: 2px;
  }
  .contact-list {
    list-style: none;
    margin-top: 18px;
    font-size: 20px;
    line-height: 1.2;
  }
  .contact-list .label {
    display: inline-block;
    width: 28px;
    color: var(--brand-blue);
    font-style: italic;
  }
  .website {
    position: absolute;
    left: 210px;
    top: 306px;
    font-size: 20px;
    line-height: 1.2;
    color: var(--ink);
    letter-spacing: 0.3px;
  }
  .website .accent-pink { color: var(--brand-pink); }
  .website .accent-blue { color: var(--brand-blue); }
  .band {
    position: absolute;
    left: 0;
    right: 0;
    bottom: 0;
    height: 54px;
    background: var(--brand-pink);
  }
</style>
</head>
<body>
<main class="stage">

  <section class="card card-back" aria-label="Business card back">
    <div class="backdrop" role="img" aria-label="Soft blue background with gentle sweeping curves"></div>
    <div class="wordmark">RTMEDIA</div>
  </section>

  <section class="card card-front" aria-label="Business card front">
    <div class="wordmark">RTMEDIA</div>
    <div class="details">
      <p class="person-name">Lena Marsh</p>
      <p class="person-role">Operation Manager</p>
      <ul class="contact-list">
        <li><span class="label">T</span>0481552306</li>
        <li><span class="label">E</span>sales@rt-media.com.au</li>
      </ul>
    </div>
    <p class="website">www.<span class="accent-pink">rt</span>-<span class="accent-blue">media</span>.com.au</p>
    <div class="band"></div>
  </section>

</main>
</body>
</html>
```